Tequila Bottle Labels

We are a construction company that bottled our own tequila and would like a unique label for it! We already have our own company logo (linked below) and we want that logo somewhere on the bottle as well- it can be big or small. It was brewed & bottled in Southern California. Ideally it would have the year "2020," "Single Estate," & "100% Agave Azul" somewhere on the label.

Tequila / DMW / 2020

```html
<!DOCTYPE html>
<html lang="en">
<head>
<meta charset="utf-8">
<title>DMW Tequila Blanco 2020 Label</title>
<link rel="stylesheet" href="https://fonts.googleapis.com/css2?family=Cinzel:wght@400&family=Tinos:wght@700&display=swap">
<style>
  :root {
    --label-navy: #254559;
    --agave-turquoise: #00e5d4;
    --lime-green: #8fd11a;
    --label-white: #ffffff;
  }
  html, body {
    margin: 0;
    padding: 0;
    width: 1200px;
    height: 1139px;
    overflow: hidden;
    background: var(--label-navy);
  }
  .label {
    display: block;
    width: 1200px;
    height: 1139px;
  }
  .label-background { fill: var(--label-navy); }
  .label-frame {
    fill: none;
    stroke: var(--lime-green);
    stroke-width: 3.4;
  }
  .brand-name {
    font-family: "Tinos", serif;
    font-weight: 700;
    font-size: 230px;
    fill: var(--agave-turquoise);
  }
  .vintage-year {
    font-family: "Tinos", serif;
    font-weight: 700;
    font-size: 86px;
    fill: var(--lime-green);
  }
  .spirit-name {
    font-family: "Cinzel", serif;
    font-weight: 400;
    font-size: 84px;
    fill: var(--lime-green);
  }
  .detail-line {
    font-family: "Tinos", serif;
    font-weight: 700;
  }
  .detail-azul { font-size: 46px; fill: var(--agave-turquoise); }
  .detail-style { font-size: 46px; fill: var(--label-white); }
  .detail-agave { font-size: 52px; fill: var(--lime-green); }
  .detail-footer { font-size: 40px; fill: var(--agave-turquoise); }
</style>
</head>
<body>
<svg class="label" viewBox="0 0 1200 1139" xmlns="http://www.w3.org/2000/svg">
  <rect class="label-background" x="0" y="0" width="1200" height="1139"/>
  <rect class="label-frame" x="56" y="56" width="1088" height="1029"/>

  <text class="brand-name" x="600" y="550" text-anchor="middle">DMW</text>

  <text class="vintage-year" x="1040" y="639" text-anchor="end">2020</text>

  <text class="spirit-name" x="600" y="744" text-anchor="middle">Tequila</text>

  <text class="detail-line detail-azul" x="628" y="828" text-anchor="middle">100% agave azul</text>
  <text class="detail-line detail-style" x="620" y="896" text-anchor="middle">TEQUILA BLANCO</text>
  <text class="detail-line detail-agave" x="620" y="972" text-anchor="middle">100% agave</text>

  <text class="detail-line detail-footer" x="103" y="1043">40% alcohol</text>
  <text class="detail-line detail-footer" x="1102" y="1043" text-anchor="end">750ml</text>
</svg>
</body>
</html>
```